Corvane Holdings , new business card design

investment firm with corporate clients . need double sided business card , vertical and horizontal options ,logo must be clear. prefer pantone colors only and sharp design. website also www.corvane.ae

Khalid Bin Tarrafi
Managing Director
Tel. +971 4 387 2940
Mobile +971 50 518 2403
khalid@corvane.ae
Q-Span Plaza, officw 18-B07, Warqa Gardens, Dubai

Contact Information for Business Card

Khalid Bin Tarrafi
Managing Director

Font styles to use
Serif

Colors

Designer to choose colors to be used in the design.

```html
<!DOCTYPE html>
<html lang="en">
<head>
<meta charset="utf-8">
<title>Corvane Holdings — Business Card</title>
<link rel="stylesheet" href="https://fonts.googleapis.com/css2?family=Jost:wght@300;400&display=swap">
<style>
  :root {
    --stage: #1e1e1e;
    --card-deep: #45709a;
    --card-light: #5a84aa;
    --ink: #ffffff;
  }
  * { margin: 0; padding: 0; box-sizing: border-box; }
  html, body {
    width: 1200px; height: 900px; overflow: hidden;
    background: var(--stage);
    font-family: "Jost", "Futura", sans-serif;
    color: var(--ink);
  }
  .stage {
    width: 1200px; height: 900px;
    display: flex; flex-direction: column;
    align-items: center; justify-content: center; gap: 40px;
  }
  .card {
    position: relative;
    width: 700px; height: 400px;
    background: linear-gradient(135deg, var(--card-deep) 0%, var(--card-light) 100%);
  }
  .wordmark {
    display: flex; flex-direction: column; align-items: center;
    font-weight: 300; color: var(--ink); line-height: 1;
  }
  .wordmark__main { letter-spacing: 0.38em; margin-right: -0.38em; }
  .wordmark__sub { letter-spacing: 0.62em; margin-right: -0.62em; }

  .card--front { display: flex; align-items: center; justify-content: center; }
  .card--front .wordmark__main { font-size: 62px; }
  .card--front .wordmark__sub { font-size: 20px; margin-top: 16px; }

  .card--back { display: flex; align-items: center; }
  .card--back .wordmark { width: 330px; }
  .card--back .wordmark__main { font-size: 40px; }
  .card--back .wordmark__sub { font-size: 13px; margin-top: 12px; }
  .divider { width: 1px; height: 190px; background: var(--ink); }
  .contact { padding-left: 40px; font-weight: 400; }
  .contact__name { font-size: 19px; text-transform: uppercase; letter-spacing: 0.02em; }
  .contact__title { font-size: 16px; margin-top: 2px; }
  .contact__address { font-size: 16px; margin-top: 16px; line-height: 1.3; }
  .contact__list { list-style: none; margin-top: 10px; font-size: 17px; line-height: 1.45; }
  .contact__list li { display: flex; align-items: center; gap: 12px; }
  .contact__icon { width: 11px; height: 11px; flex: none; }
</style>
</head>
<body>
<main class="stage">
  <section class="card card--front" aria-label="Card front">
    <div class="wordmark">
      <span class="wordmark__main">CORVANE</span>
      <span class="wordmark__sub">HOLDINGS</span>
    </div>
  </section>

  <section class="card card--back" aria-label="Card back">
    <div class="wordmark">
      <span class="wordmark__main">CORVANE</span>
      <span class="wordmark__sub">HOLDINGS</span>
    </div>
    <div class="divider"></div>
    <div class="contact">
      <p class="contact__name">Khalid Bin Tarrafi</p>
      <p class="contact__title">Managing Director</p>
      <p class="contact__address">Q-Span Plaza, officw 18-B07,<br>Warqa Gardens, Dubai</p>
      <ul class="contact__list">
        <li>
          <svg class="contact__icon" viewBox="0 0 12 12" aria-hidden="true"><path d="M3 1 L5 3.5 L4 5 Q5.5 7.5 7 8 L8.5 7 L11 9 L10 11 Q4 11 1 2 Z" fill="none" stroke="#fff" stroke-width="1"/></svg>
          <span>+971 4 387 2940</span>
        </li>
        <li>
          <svg class="contact__icon" viewBox="0 0 12 12" aria-hidden="true"><rect x="3" y="0.5" width="6" height="11" rx="1" fill="none" stroke="#fff" stroke-width="1"/><line x1="5" y1="9.5" x2="7" y2="9.5" stroke="#fff"/></svg>
          <span>+971 50 518 2403</span>
        </li>
        <li>
          <svg class="contact__icon" viewBox="0 0 12 12" aria-hidden="true"><rect x="0.5" y="2.5" width="11" height="7" fill="none" stroke="#fff" stroke-width="1"/><path d="M0.5 2.5 L6 6.5 L11.5 2.5" fill="none" stroke="#fff" stroke-width="1"/></svg>
          <span>khalid@corvane.ae</span>
        </li>
      </ul>
    </div>
  </section>
</main>
</body>
</html>
```